Modern Business Card for Larkwell 2018

Our company assumes the best about people. We are creating an online community of entrepreneurs and business leaders who struggle with marketing their business online.

This business card should POP! We recently got a new logo and are launching a new website next month, so our business cards should make a statement that feels:
-Fresh
-Smart
-Trustworthy
-Fun

Target Market(s)

small business owners, entrepreneurs

Industry/Entity Type

Digital Marketing

Contact Information for Business Card

Dimensions: 3.5" x 2"

Font styles to use
Sans Serif

Colors
f37122
ffffff

Requirements
Must have
• We need a business card with a modern, bold design. We will use one side of the card as a lead-generation offer, so text on one side will need to fit up to 140 characters. The business card should stick to our core colors (orange, black, and white).
Nice to have
• We think a vertical "portrait" design could be interesting.
Should not have
• Should not look like a traditional business card. The round icon should stand out from a distance.

```html
<!DOCTYPE html>
<html lang="en">
<head>
<meta charset="utf-8">
<title>Larkwell Business Card</title>
<link rel="stylesheet" href="https://fonts.googleapis.com/css2?family=Niconne&family=Roboto:wght@400;500;700&display=swap">
<style>
  :root {
    --orange: #f26a27;
    --black: #000000;
    --white: #ffffff;
    --card: #f7f7f7;
    --ink: #111111;
    --backdrop: #e8e5e1;
    --rule: #333333;
  }
  * { margin: 0; padding: 0; box-sizing: border-box; }
  html, body { width: 1200px; height: 960px; overflow: hidden; }
  body {
    position: relative;
    background: var(--backdrop);
    font-family: "Roboto", Arial, sans-serif;
    color: var(--ink);
  }
  .card {
    position: absolute;
    width: 600px;
    height: 342px;
    border-radius: 22px;
    background: var(--card);
    overflow: hidden;
    box-shadow: 0 3px 8px rgba(0,0,0,0.35);
  }
  .card--front { left: 314px; top: 113px; }
  .card--back { left: 311px; top: 472px; }

  .front-band {
    position: absolute; left: 0; top: 38px; width: 100%; height: 74px;
    background: var(--black);
    display: flex; align-items: center; justify-content: center;
  }
  .front-brand {
    color: var(--white); font-weight: 700; font-size: 22px; letter-spacing: 2px; line-height: 1;
  }
  .holder-name {
    position: absolute; left: 0; top: 136px; width: 100%; text-align: center;
    font-family: "Niconne", cursive; font-weight: 400; font-size: 92px; line-height: 1; color: var(--black);
  }
  .holder-email {
    position: absolute; left: 0; top: 250px; width: 100%; text-align: center;
    font-size: 15px; font-weight: 500;
  }
  .holder-role {
    position: absolute; left: 0; top: 283px; width: 100%; text-align: center;
    font-size: 19px; font-weight: 500; letter-spacing: 0.3px;
  }

  .back-panel {
    position: absolute; left: 0; top: 0; width: 100%; height: 218px;
    background: var(--orange); color: var(--white);
  }
  .brand {
    position: absolute; left: 40px; top: 110px; width: 238px; text-align: center;
  }
  .brand-name { font-size: 38px; font-weight: 700; letter-spacing: 2.5px; line-height: 1; }
  .brand-tagline { font-size: 11px; font-weight: 500; letter-spacing: 0.9px; margin-top: 8px; }
  .panel-divider {
    position: absolute; left: 297px; top: 28px; width: 1px; height: 165px;
    background: rgba(255,255,255,0.6);
  }
  .offer { position: absolute; left: 323px; top: 29px; width: 270px; }
  .offer-headline { font-size: 19.5px; font-weight: 500; line-height: 21px; letter-spacing: 0.2px; }
  .offer-body { font-size: 16px; line-height: 19px; margin-top: 6px; }
  .offer-url { font-size: 20px; font-weight: 700; margin-top: 9px; }

  .note-line {
    position: absolute; left: 36px; width: 519px; height: 1px; background: var(--rule);
  }
  .note-line--1 { top: 260px; }
  .note-line--2 { top: 300px; }
</style>
</head>
<body>
  <section class="card card--front">
    <div class="front-band"><span class="front-brand">LARKWELL</span></div>
    <h1 class="holder-name">Miles Hartley</h1>
    <p class="holder-email">miles@larkwellnow.com</p>
    <p class="holder-role">STORY MARKETING COACH</p>
  </section>

  <section class="card card--back">
    <div class="back-panel">
      <div class="brand">
        <div class="brand-name">LARKWELL</div>
        <div class="brand-tagline">TELL STORIES THAT INSPIRE ACTION</div>
      </div>
      <div class="panel-divider"></div>
      <div class="offer">
        <p class="offer-headline">REACH MORE PEOPLE.<br>MAKE MORE MONEY.<br>CREATE MORE IMPACT.</p>
        <p class="offer-body">Get your free Larkwell<br>Starter Package and our<br>marketing guide today at</p>
        <p class="offer-url">Larkwellnow.com/start</p>
      </div>
    </div>
    <div class="note-line note-line--1"></div>
    <div class="note-line note-line--2"></div>
  </section>
</body>
</html>
```